Animal Eye Clinic needs a Business card

We are a new veterinary ophthalmology practice (Ridgeline Pet Vision Care) and we need a business card designed. We only see animal eyes - we are not a regular veterinary clinic. We already have a logo. We are looking for a professional, good looking business card to hand out to our clients. We are looking for something simple but professional and contemporary. Our logo is likely the only picture/graphic that needs to be on the card.
Updates

Contact Information for Business Card

Delia Vossman, BSc, DVM, MSc, DipACVO
Veterinary Ophthalmologist

Phone: 250.418.3927
Email: ridgelinepetvisioncare@mailbox-example.net
Website: ridgelinepetvisioncare-example.net
Address: 1874 Thornbury Rd
Kelowna, BC, V1X 4M9

Colors

Designer to choose colors to be used in the design.

Requirements
Must have
• Our logo (attached)

```html
<!DOCTYPE html>
<html lang="en">
<head>
<meta charset="utf-8">
<title>Ridgeline Pet Vision Care – Business Card</title>
<link rel="stylesheet" href="https://fonts.googleapis.com/css2?family=Montserrat:wght@400;500;600&display=swap">
<style>
  :root {
    --teal: #1598a8;
    --text-grey: #5f6163;
    --paper: #ffffff;
    --card-dark: #1a1a1a;
    --page: #ffffff;
    --shadow: rgba(0,0,0,0.28);
  }
  * { margin: 0; padding: 0; box-sizing: border-box; }
  html, body {
    width: 1200px; height: 1200px; overflow: hidden;
    background: var(--page);
    font-family: "Montserrat", Arial, sans-serif;
  }
  .canvas { position: relative; width: 1200px; height: 1200px; }

  .card {
    position: absolute;
    width: 836px; height: 478px;
    box-shadow: 0 2px 10px var(--shadow);
  }
  .card--front { left: 185px; top: 82px; background: var(--paper); }
  .card--back { left: 187px; top: 625px; background: var(--card-dark); }

  /* brand name lockup */
  .brand {
    position: absolute;
    display: flex; align-items: center; gap: 18px;
    color: var(--teal);
    font-weight: 600;
    font-size: 33px;
    line-height: 1.08;
    letter-spacing: 0.5px;
    text-transform: uppercase;
  }
  .brand__dot {
    width: 66px; height: 66px; border-radius: 50%;
    background: var(--teal); flex: none;
  }
  .card--front .brand { right: 28px; top: 46px; }
  .card--back .brand { left: 32px; top: 340px; }

  /* person block */
  .person {
    position: absolute; left: 0; top: 255px;
    padding-left: 30px;
    border-left: 8px solid var(--teal);
  }
  .person__name {
    color: var(--teal);
    font-weight: 600;
    font-size: 32px;
    line-height: 1;
    letter-spacing: 0.3px;
    margin-top: -4px;
  }
  .person__credentials, .person__role {
    color: var(--text-grey);
    font-size: 19px;
    line-height: 26px;
  }
  .person__credentials { margin-top: 6px; }

  /* contact list */
  .contact {
    position: absolute; left: 30px; top: 362px;
    list-style: none;
  }
  .contact__item {
    display: flex; align-items: center; gap: 11px;
    height: 30px;
    color: var(--text-grey);
    font-size: 16.5px;
  }
  .contact__icon { width: 21px; height: 21px; flex: none; fill: var(--teal); }

  /* address */
  .address {
    position: absolute; right: 28px; top: 358px;
    text-align: right; font-style: normal;
  }
  .address__company {
    color: var(--teal);
    font-weight: 600;
    font-size: 18px;
    letter-spacing: 0.6px;
    line-height: 26px;
    text-transform: uppercase;
  }
  .address__line {
    color: var(--text-grey);
    font-size: 19px;
    line-height: 30px;
  }
</style>
</head>
<body>
<div class="canvas">

  <section class="card card--front">
    <div class="brand">
      <span class="brand__dot"></span>
      <span class="brand__name">Ridgeline<br>Pet Vision Care</span>
    </div>

    <div class="person">
      <h1 class="person__name">DELIA VOSSMAN</h1>
      <p class="person__credentials">BSc, DVM, MSc, DipACVO</p>
      <p class="person__role">Veterinary Ophthalmologist</p>
    </div>

    <ul class="contact">
      <li class="contact__item">
        <svg class="contact__icon" viewBox="0 0 24 24" aria-hidden="true"><path d="M6.6 10.8a15.1 15.1 0 0 0 6.6 6.6l2.2-2.2c.3-.3.7-.4 1-.2 1.1.4 2.3.6 3.6.6.6 0 1 .4 1 1V20c0 .6-.4 1-1 1C10.6 21 3 13.4 3 4c0-.6.4-1 1-1h3.5c.6 0 1 .4 1 1 0 1.3.2 2.5.6 3.6.1.3 0 .7-.2 1z"/></svg>
        <span>250.418.3927</span>
      </li>
      <li class="contact__item">
        <svg class="contact__icon" viewBox="0 0 24 24" aria-hidden="true"><path d="M2 5h20v14H2z M2 5l10 8 10-8" fill="none" stroke="var(--teal)" stroke-width="0"/><path d="M2 5h20L12 12.5z M2 6.8l10 7.5 10-7.5V19H2z"/></svg>
        <span>ridgelinepetvisioncare@mailbox-example.net</span>
      </li>
      <li class="contact__item">
        <svg class="contact__icon" viewBox="0 0 24 24" aria-hidden="true"><circle cx="12" cy="12" r="10"/><path d="M12 2v20M2 12h20" stroke="#fff" stroke-width="1.2"/><ellipse cx="12" cy="12" rx="4.5" ry="10" fill="none" stroke="#fff" stroke-width="1.2"/></svg>
        <span>www.ridgelinepetvisioncare-example.net</span>
      </li>
    </ul>

    <address class="address">
      <p class="address__company">Ridgeline Pet Vision Care</p>
      <p class="address__line">1874 Thornbury Rd</p>
      <p class="address__line">Kelowna, BC, V1X 4M9</p>
    </address>
  </section>

  <section class="card card--back">
    <div class="brand">
      <span class="brand__dot"></span>
      <span class="brand__name">Ridgeline<br>Pet Vision Care</span>
    </div>
  </section>

</div>
</body>
</html>
```